Web design for a honey company

We are a honey retailing company currently looking for creative design for 3 pages of our existing e-commerce website which can be found here www.alpha.tolvenmarsk.co.nz. The designs need to be responsive i.e. presented in both desktop and mobile versions. We want to use the existing page color pallet, however any fonts can be used. Please use the texts and graphic content in the attachment files provided. For more detailed instructions please. The page does not require coding, the output files should be provided as layered and editable PSD.<br/><br/>Task 2: design 2 home page banners. Images, texts and the concept provided in the "layout structure" file. <br/><br/>The web designs should be presented in both desktop and mobile versions. We are looking for professional designer submissions only!

Target Market(s)

Hi-end consumers
Health conscious consumers

Number of Pages Required

3 page

Requirements
Must have
• 50% of images supplied along + any suggested stock images.
• Supplied texts integrated in the designs.
• Please only use the product images we have provided!
Should not have
• Clipart vector bees, vector honey slots or combs.
• No images of honey in glass jars!
• Do not use images of the traditional honey wooden spoons!
• Do not use images of any other but Manuka flower!

```html
<!DOCTYPE html>
<html lang="en">
<head>
<meta charset="utf-8">
<title>Tolvenmarsk – Manuka Honey</title>
<link rel="stylesheet" href="https://fonts.googleapis.com/css2?family=Tinos&family=Lato:wght@400;700&display=swap">
<style>
:root{
  --navy:#0b0f1e;
  --navy-2:#141a2e;
  --gold:#d4ad4e;
  --gold-light:#f5dc8e;
  --gold-dark:#b38a2c;
  --page:#f3f3f3;
  --ink:#1b1b1b;
  --muted:#3a3a3a;
  --white:#ffffff;
}
*{box-sizing:border-box;margin:0;padding:0}
html,body{width:1200px;height:4132px;overflow:hidden;background:var(--page)}
body{font-family:"Lato",sans-serif;color:var(--ink)}
.canvas{position:relative;width:1200px;height:4132px;overflow:hidden;background:var(--page)}
.abs{position:absolute}
.serif{font-family:"Tinos",serif;font-weight:400}
.btn{position:absolute;display:flex;align-items:center;justify-content:center;
  background:linear-gradient(180deg,var(--gold-light),var(--gold));color:#2a1e05;
  font-family:"Tinos",serif;font-size:11px;letter-spacing:.5px;text-transform:uppercase;height:32px;width:120px}
.section-title{position:absolute;left:0;width:1200px;text-align:center;font-family:"Tinos",serif;font-size:30px;letter-spacing:1px;color:var(--ink)}

/* header */
.site-header{position:absolute;left:0;top:0;width:1200px;height:60px;background:var(--navy);border-bottom:4px solid var(--gold)}
.brand-tab{position:absolute;left:516px;top:0;width:170px;height:100px;background:var(--navy);border:4px solid var(--gold);border-top:none;border-radius:0 0 85px 85px;display:flex;align-items:center;justify-content:center}
.brand-name{font-family:"Tinos",serif;color:var(--gold);font-size:17px;letter-spacing:1.5px}
.header-icons{position:absolute;top:20px;right:110px;display:flex;gap:18px;align-items:center;color:var(--gold)}
.login-label{font-size:12px;color:var(--gold);margin-left:4px}

/* hero */
.hero-bg{position:absolute;left:0;top:64px;width:1200px;height:720px;
  background:radial-gradient(ellipse at 12% 20%,#ffffff 0%,#f1f1f3 35%,transparent 60%),
  radial-gradient(ellipse at 30% 90%,#c9cdb8 0%,transparent 45%),
  linear-gradient(90deg,#e6e4ea 0%,#f7f7f8 45%,#ffffff 100%)}
.hero-products{position:absolute;left:575px;top:195px;width:570px;height:400px;border-radius:14px;
  background:linear-gradient(135deg,#1a1410 0%,#2b2016 40%,#3c2a30 70%,#e9b9c6 100%)}
.hero-kicker{position:absolute;left:106px;top:325px;font-family:"Tinos",serif;font-size:35px;color:var(--ink)}
.hero-title{position:absolute;left:106px;top:362px;font-family:"Tinos",serif;font-size:56px;color:var(--ink)}
.hero-sub{position:absolute;left:106px;top:430px;font-size:13px;color:var(--muted)}

/* products */
.product{position:absolute;top:950px;width:340px;text-align:center}
.product-shot{margin:0 auto;width:200px;height:235px;border-radius:10px;background:linear-gradient(160deg,#2a2018,#0f0c0a 60%,#3b5f5a)}
.product-name{margin-top:62px;font-family:"Tinos",serif;font-size:18px;color:var(--ink)}
.product-price{margin-top:10px;font-size:13px;color:var(--ink)}
.product .btn{position:static;margin:22px auto 0}

/* about */
.about-band{position:absolute;left:0;top:1400px;width:1200px;height:680px;background:var(--navy)}
.about-visual{position:absolute;left:96px;top:1490px;width:418px;height:570px;
  background:linear-gradient(180deg,#d68a1e 0%,#c2741a 35%,#2a1c12 60%,#120d0a 100%);border-radius:0 0 6px 6px}
.about-title{position:absolute;left:605px;top:1530px;font-family:"Tinos",serif;font-size:30px;color:var(--white)}
.about-text{position:absolute;left:606px;top:1642px;width:450px;font-size:12.6px;line-height:26.3px;color:#e8e8e8}

/* articles */
.article{position:absolute;width:470px}
.article-photo{width:470px;height:280px}
.article-title{margin-top:30px;font-family:"Tinos",serif;font-size:20px;color:var(--ink);padding-left:2px}
.article-text{margin-top:18px;font-size:10.6px;line-height:22.5px;color:var(--muted);padding-left:2px}
.article .btn{position:static;margin-top:28px}
.play{position:absolute;left:195px;top:110px;width:80px;height:60px;border-radius:14px;background:rgba(0,0,0,.78)}

/* newsletter */
.signup-field{position:absolute;left:361px;top:3545px;width:345px;height:32px;background:var(--navy);color:#e6e6e6;font-size:11px;display:flex;align-items:center;padding-left:14px;gap:8px}
.signup-btn{left:717px;top:3545px;width:120px}

/* footer */
.footer-band{position:absolute;left:0;top:3640px;width:1200px;height:450px;background:var(--navy)}
.footer-brand{position:absolute;left:106px;top:3790px;font-family:"Tinos",serif;color:var(--gold);font-size:24px;letter-spacing:1.5px}
.footer-about{position:absolute;left:106px;top:3883px;width:245px;font-size:11px;line-height:22.5px;color:#e6e6e6}
.pay-cards{position:absolute;left:106px;top:3990px;display:flex;gap:8px}
.pay-card{width:40px;height:25px;background:#f4f4f4;border-radius:2px}
.footer-col{position:absolute;top:3795px}
.footer-heading{font-family:"Tinos",serif;font-size:17px;color:var(--white);letter-spacing:.5px}
.footer-list{list-style:none;margin-top:70px;font-size:11px;line-height:22.5px;color:#e6e6e6}
.contact-row{display:flex;gap:8px;align-items:flex-start}
.bottom-bar{position:absolute;left:0;top:4082px;width:1200px;height:50px;background:linear-gradient(180deg,var(--gold-light),var(--gold))}
.copyright{position:absolute;left:106px;top:18px;font-size:11px;color:#2a1e05}
.socials{position:absolute;right:106px;top:13px;display:flex;gap:9px}
.social{width:24px;height:24px;border:1.5px solid #2a1e05;border-radius:50%}
</style>
</head>
<body>
<div class="canvas">

  <!-- header -->
  <header class="site-header">
    <svg class="abs" style="left:106px;top:22px" width="20" height="16" viewBox="0 0 20 16"><path d="M0 1h20M0 8h20M0 15h20" stroke="#d4ad4e" stroke-width="1.6"/></svg>
    <div class="header-icons">
      <span style="display:flex;align-items:center">
        <svg width="16" height="16" viewBox="0 0 16 16" fill="none" stroke="#d4ad4e" stroke-width="1.3"><circle cx="8" cy="5" r="3.5"/><path d="M1.5 15.5c.8-4 3.3-5.5 6.5-5.5s5.7 1.5 6.5 5.5"/></svg>
        <span class="login-label">Login</span>
      </span>
      <svg width="18" height="16" viewBox="0 0 18 16" fill="none" stroke="#d4ad4e" stroke-width="1.4"><path d="M9 15S1 10 1 5a4 4 0 0 1 8-1 4 4 0 0 1 8 1c0 5-8 10-8 10z"/></svg>
      <svg width="20" height="18" viewBox="0 0 20 18" fill="none" stroke="#d4ad4e" stroke-width="1.4"><path d="M1 1h3l2.5 11h10L19 4H5"/><circle cx="8" cy="16" r="1.3"/><circle cx="15" cy="16" r="1.3"/></svg>
    </div>
  </header>

  <!-- hero -->
  <div class="hero-bg" role="img" aria-label="Soft-focus white manuka blossoms"></div>
  <div class="hero-products" role="img" aria-label="Four jars of manuka honey with pink manuka flowers"></div>
  <div class="brand-tab"><span class="brand-name">TOLVENMARSK</span></div>
  <div class="hero-kicker">THE PUREST TASTE OF</div>
  <div class="hero-title">NEW ZEALAND</div>
  <div class="hero-sub">100% New Zealand Manuka Honey</div>
  <div class="btn" style="left:106px;top:465px">Buy now</div>

  <svg class="abs" style="left:0;top:640px" width="1200" height="150" viewBox="0 0 1200 150">
    <path d="M0 85 C 250 160, 650 40, 900 50 S 1150 65, 1200 75 L1200 150 L0 150 Z" fill="#f3f3f3"/>
    <path d="M0 85 C 250 160, 650 40, 900 50 S 1150 65, 1200 75" fill="none" stroke="#d4ad4e" stroke-width="7"/>
  </svg>

  <!-- featured products -->
  <h2 class="section-title" style="top:835px">FEATURED PRODUCTS</h2>

  <div class="product" style="left:83px">
    <div class="product-shot" role="img" aria-label="Jar of MGO 400+ manuka honey with grade badge"></div>
    <div class="product-name">MGO 400+ MANUKA HONEY</div>
    <div class="product-price">USD $25.00 – USD $35.00</div>
    <div class="btn">Shop now</div>
  </div>
  <div class="product" style="left:425px">
    <div class="product-shot" role="img" aria-label="Jar of MGO 800+ manuka honey with grade badge"></div>
    <div class="product-name">MGO 800+ MANUKA HONEY</div>
    <div class="product-price">USD $25.00 – USD $129.00</div>
    <div class="btn">Shop now</div>
  </div>
  <div class="product" style="left:775px">
    <div class="product-shot" role="img" aria-label="Jar of MGO 500+ manuka honey with grade badge"></div>
    <div class="product-name">MGO 500+ MANUKA HONEY</div>
    <div class="product-price">USD $25.00 – USD $35.00</div>
    <div class="btn">Shop now</div>
  </div>

  <!-- about -->
  <div class="about-band"></div>
  <svg class="abs" style="left:0;top:1398px" width="1200" height="115" viewBox="0 0 1200 115">
    <path d="M0 0 H1200 V15 C 1000 0, 750 40, 450 85 C 250 112, 80 100, 0 62 Z" fill="#f3f3f3"/>
    <path d="M1200 15 C 1000 0, 750 40, 450 85 C 250 112, 80 100, 0 62" fill="none" stroke="#d4ad4e" stroke-width="7"/>
  </svg>
  <div class="about-visual" role="img" aria-label="Golden manuka honey pouring from a spoon into a dark jar"></div>
  <svg class="abs" style="left:0;top:1975px" width="1200" height="110" viewBox="0 0 1200 110">
    <path d="M0 50 C 80 100, 200 95, 450 55 C 750 10, 1000 0, 1200 15 V110 H0 Z" fill="#f3f3f3"/>
    <path d="M0 50 C 80 100, 200 95, 450 55 C 750 10, 1000 0, 1200 15" fill="none" stroke="#d4ad4e" stroke-width="7"/>
  </svg>
  <h2 class="about-title">ABOUT US</h2>
  <p class="about-text">Lorem Ipsum is simply dummy text of the printing and typesetting industry. Lorem Ipsum has been the industry's standard dummy text ever since the 1500s, when an unknown printer took a galley of type and scrambled it to make a type specimen book. It has survived not only five centuries, but also the leap into electronic typesetting, remaining essentially unchanged. It was popularised in the 1960s with the release of Letraset sheets containing Lorem Ipsum passages, and more recently with desktop publishing software like Aldus PageMaker including versions of Lorem Ipsum.</p>
  <div class="btn" style="left:606px;top:1880px">Read more</div>

  <!-- articles -->
  <h2 class="section-title" style="top:2122px">LATEST ARTICLES</h2>

  <article class="article" style="left:106px;top:2242px">
    <div class="article-photo" role="img" aria-label="Beekeeper in yellow gloves holding a hive frame" style="background:linear-gradient(135deg,#6b5a3c,#9a7b48 40%,#d7b63e 75%,#8c7a55)"></div>
    <h3 class="article-title">ARTICLE TITLE # 01</h3>
    <p class="article-text">Lorem Ipsum is simply dummy text of the printing and typesetting industry. Lorem Ipsum has been the industry's standard dummy text ever since the 1500s, when an unknown printer took a galley of type and scrambled it to make a type specimen book.</p>
    <div class="btn">Read more</div>
  </article>
  <article class="article" style="left:624px;top:2242px">
    <div class="article-photo" role="img" aria-label="Bee on a bright yellow flower" style="background:radial-gradient(ellipse at 55% 60%,#f2e21a 0%,#f5ef7a 30%,#f7f5e9 65%,#f3f1ea 100%)"></div>
    <h3 class="article-title">ARTICLE TITLE # 02</h3>
    <p class="article-text">Lorem Ipsum is simply dummy text of the printing and typesetting industry. Lorem Ipsum has been the industry's standard dummy text ever since the 1500s, when an unknown printer took a galley of type and scrambled it to make a type specimen book.</p>
    <div class="btn">Read more</div>
  </article>
  <article class="article" style="left:106px;top:2804px">
    <div class="article-photo" role="img" aria-label="Video still of a beekeeper in a white suit tending hives" style="position:relative;background:linear-gradient(120deg,#3e4a2a,#7b8a5e 45%,#d9dde0 70%,#b7bcc2)">
      <span class="play"></span>
      <svg class="abs" style="left:226px;top:128px" width="20" height="24" viewBox="0 0 20 24"><path d="M0 0L20 12L0 24Z" fill="#fff"/></svg>
    </div>
    <h3 class="article-title">ARTICLE TITLE # 03</h3>
    <p class="article-text">Lorem Ipsum is simply dummy text of the printing and typesetting industry. Lorem Ipsum has been the industry's standard dummy text ever since the 1500s, when an unknown printer took a galley of type and scrambled it to make a type specimen book.</p>
    <div class="btn">Read more</div>
  </article>
  <article class="article" style="left:624px;top:2804px">
    <div class="article-photo" role="img" aria-label="Bumblebee visiting a white manuka blossom" style="background:radial-gradient(ellipse at 60% 50%,#ecebe6 0%,#8c8f7a 40%,#3d4234 100%)"></div>
    <h3 class="article-title">ARTICLE TITLE # 04</h3>
    <p class="article-text">Lorem Ipsum is simply dummy text of the printing and typesetting industry. Lorem Ipsum has been the industry's standard dummy text ever since the 1500s, when an unknown printer took a galley of type and scrambled it to make a type specimen book.</p>
    <div class="btn">Read more</div>
  </article>

  <!-- newsletter -->
  <h2 class="section-title" style="top:3414px">SIGNUP FOR OUR NEWSLETTER</h2>
  <div class="signup-field">
    <svg width="12" height="9" viewBox="0 0 12 9"><rect x=".5" y=".5" width="11" height="8" fill="#e6e6e6"/><path d="M.5 .5L6 5L11.5 .5" fill="none" stroke="#0b0f1e"/></svg>
    Email Address
  </div>
  <div class="btn signup-btn">Signup</div>

  <!-- footer -->
  <div class="footer-band"></div>
  <svg class="abs" style="left:0;top:3630px" width="1200" height="115" viewBox="0 0 1200 115">
    <path d="M0 0 H1200 V12 C 950 15, 650 55, 400 85 C 220 105, 80 85, 0 55 Z" fill="#f3f3f3"/>
    <path d="M1200 12 C 950 15, 650 55, 400 85 C 220 105, 80 85, 0 55" fill="none" stroke="#d4ad4e" stroke-width="7"/>
  </svg>

  <div class="footer-brand">TOLVENMARSK</div>
  <p class="footer-about">Lorem Ipsum is simply dummy text of the printing and typesetting industry. Lorem Ipsum has been the industry's standard dummy text ever since the 1500s.</p>
  <div class="pay-cards" aria-label="Accepted payment cards">
    <span class="pay-card"></span><span class="pay-card"></span><span class="pay-card"></span>
  </div>

  <div class="footer-col" style="left:417px">
    <h4 class="footer-heading">QUICK LINKS</h4>
    <ul class="footer-list"><li>Home</li><li>Shop</li><li>Quality</li><li>About Tolvenmarsk</li><li>Articles</li><li>Contact Us</li></ul>
  </div>
  <div class="footer-col" style="left:595px">
    <h4 class="footer-heading">ACCOUNTS</h4>
    <ul class="footer-list"><li>Login</li><li>Signup</li><li>My Profile</li><li>My cart</li><li>Whishlist</li><li>Checkout</li></ul>
  </div>
  <div class="footer-col" style="left:752px">
    <h4 class="footer-heading">CONTACT US</h4>
    <ul class="footer-list">
      <li class="contact-row"><svg width="12" height="12" viewBox="0 0 12 12" style="margin-top:5px"><path d="M2 1l2 0 1 3-1.5 1a7 7 0 0 0 3.5 3.5L8 7l3 1v2a1 1 0 0 1-1 1C5 11 1 7 1 2a1 1 0 0 1 1-1z" fill="#d4ad4e"/></svg>+(64) 210004417</li>
      <li class="contact-row"><svg width="12" height="9" viewBox="0 0 12 9" style="margin-top:7px"><rect width="12" height="9" fill="#d4ad4e"/><path d="M0 0L6 5L12 0" fill="none" stroke="#0b0f1e"/></svg>sales@tolvenmarsk.co.nz</li>
      <li class="contact-row"><svg width="12" height="14" viewBox="0 0 12 14" style="margin-top:5px"><path d="M6 14S1 8.5 1 5a5 5 0 0 1 10 0c0 3.5-5 9-5 9z" fill="#d4ad4e"/><circle cx="6" cy="5" r="1.8" fill="#0b0f1e"/></svg><span>Postal adress: 42 Harbourline Rd,<br>Tauranga 3110, New Zealand</span></li>
    </ul>
  </div>
  <div class="footer-col" style="left:987px">
    <h4 class="footer-heading">LINKS</h4>
    <ul class="footer-list"><li>Terms &amp; Conditions</li><li>Privacy Policy</li><li>FAQs</li><li>Partnership enquiries</li></ul>
  </div>

  <div class="bottom-bar">
    <span class="copyright">Copyright © 2020 Tolvenmarsk Health Limited. All Right Reserved.</span>
    <div class="socials" aria-label="Social media links">
      <span class="social"></span><span class="social"></span><span class="social"></span><span class="social"></span><span class="social"></span>
    </div>
  </div>

</div>
</body>
</html>
```